Template Flyer- Corewell Stretch & Flow

I am wanting a template 1 page flyer designed to use on the back ground of newsletter (faded background) and for our advertising posters in A4, A3, for Facebook and Instagram compatibility.

I have loaded an example from another Studio called Pinegrove (file 3)- each time they have a new workshop to advertise a picture is placed in the little circle (so this is something I would want to do too where I can load a new picture each time a new workshop is running)- They have used the flyer like a water mark...I like this.

Our colour palette is what is on our logos and you can also visit our website for a feel for what we like www.corewellstretch.com.au

I need some of the designs edited a bit more and because of the time difference, there seems to be a 24hour period where we communicate with each other. May I please request another 2 days extension

Requirements
Must have
• Id like to have a picture in the back ground. My favourite back ground that has been produced so far is a background of both picture file 9 and 10 in either.
Nice to have
• 3 picture circles options to advertise the events/workshops I have each year.
• Brush stroke style circles (see picture attached)rather then smooth circles for the picture area (in a grey tone)
Should not have
• No BLACK colour writing or black circles

```html
<!DOCTYPE html>
<html lang="en">
<head>
<meta charset="utf-8">
<title>Yoga &amp; Pilates Workshop, Gisborne – Corewell Stretch &amp; Flow</title>
<link rel="stylesheet" href="https://fonts.googleapis.com/css2?family=Quicksand:wght@600;700&family=Open+Sans:wght@600;700&display=swap">
<style>
  :root {
    --teal: #1a8db0;
    --taupe: #b9afa3;
    --ring-grey: #857c76;
    --paper: #d9d5d2;
    --ink: #4a433d;
    --white: #ffffff;
  }
  * { margin: 0; padding: 0; box-sizing: border-box; }
  html, body { width: 960px; height: 1200px; overflow: hidden; background: var(--paper); }
  .flyer {
    position: relative;
    width: 960px;
    height: 1200px;
    overflow: hidden;
    font-family: "Open Sans", sans-serif;
  }
  .flyer__art { position: absolute; inset: 0; width: 960px; height: 1200px; }
  .headline {
    position: absolute;
    top: 30px;
    left: 0;
    width: 960px;
    text-align: center;
    font-family: "Quicksand", sans-serif;
    font-weight: 700;
    color: var(--teal);
    line-height: 1;
  }
  .headline__top { display: block; font-size: 62px; }
  .headline__bottom { display: block; font-size: 64px; margin-top: 10px; }
  .band-text {
    position: absolute;
    left: 0;
    width: 960px;
    text-align: center;
    font-weight: 700;
    line-height: 1.2;
  }
  .band-text--date { top: 733px; color: var(--ink); }
  .band-text--date .date { display: block; font-size: 25px; }
  .band-text--date .time { display: block; font-size: 18px; margin-top: 4px; }
  .band-text--venue { top: 812px; color: var(--white); font-size: 18px; }
  .band-text--price { top: 884px; color: var(--ink); }
  .band-text--price .label { display: block; font-size: 24px; letter-spacing: 0.5px; }
  .band-text--price .amount { display: block; font-size: 18px; margin-top: 4px; }
  .band-text--booking { top: 1023px; color: var(--white); font-size: 25px; }
  .studio-name {
    position: absolute;
    top: 1116px;
    left: 0;
    width: 960px;
    display: flex;
    justify-content: center;
    align-items: center;
    gap: 14px;
    font-weight: 600;
    font-size: 30px;
    color: var(--ink);
  }
  .studio-name__dot {
    width: 46px;
    height: 46px;
    border-radius: 50%;
    border: 3px solid var(--ink);
  }
</style>
</head>
<body>
<main class="flyer">
  <svg class="flyer__art" viewBox="0 0 960 1200" xmlns="http://www.w3.org/2000/svg">
    <defs>
      <radialGradient id="bg-photo" cx="0.5" cy="0.5" r="0.75">
        <stop offset="0" stop-color="#e2ddd8"/>
        <stop offset="0.35" stop-color="#d3c8bd"/>
        <stop offset="0.6" stop-color="#c4bab1"/>
        <stop offset="1" stop-color="#cfcac6"/>
      </radialGradient>
      <linearGradient id="studio-photo" x1="0" y1="0" x2="1" y2="1">
        <stop offset="0" stop-color="#d2cec9"/>
        <stop offset="0.45" stop-color="#8e8a86"/>
        <stop offset="0.75" stop-color="#b98e62"/>
        <stop offset="1" stop-color="#6fa5a8"/>
      </linearGradient>
      <clipPath id="photo-clip">
        <ellipse cx="480" cy="445" rx="250" ry="222"/>
      </clipPath>
    </defs>

    <rect class="bg-photo" x="0" y="0" width="960" height="1200" fill="url(#bg-photo)"
          role="img" aria-label="Faded background photo of many hands reaching into a circle"/>

    <g class="outer-ring" fill="none" stroke="var(--ring-grey)" stroke-opacity="0.5" stroke-linecap="round">
      <path d="M 520 20 A 560 520 0 0 1 900 900" stroke-width="34"/>
      <path d="M 40 980 A 560 520 0 0 0 760 1140" stroke-width="30"/>
      <path d="M 250 520 A 120 60 0 0 0 150 600" stroke-width="26"/>
    </g>

    <rect class="workshop-photo" x="225" y="220" width="510" height="450" clip-path="url(#photo-clip)"
          fill="url(#studio-photo)" role="img"
          aria-label="Workshop photo: yoga mats, cork blocks and patterned bolsters in a row"/>

    <path class="photo-arc photo-arc--grey" d="M 440 214 A 262 236 0 0 1 660 640" fill="none"
          stroke="var(--taupe)" stroke-width="20" stroke-linecap="round"/>
    <path class="photo-arc photo-arc--teal" d="M 268 270 A 262 236 0 0 0 600 690 Q 700 660 752 540"
          fill="none" stroke="var(--teal)" stroke-width="14" stroke-linecap="round"/>

    <path class="band band--date" fill="var(--taupe)"
          d="M 102 744 L 300 736 L 860 733 L 820 744 L 842 752 L 800 764 L 820 780 L 770 792 L 330 802 L 200 798 L 250 790 L 150 784 L 220 772 L 130 764 L 210 754 Z"/>
    <path class="band band--venue" fill="var(--teal)"
          d="M 143 820 L 300 810 L 690 806 L 770 814 L 740 824 L 800 836 L 816 842 L 760 850 L 320 858 L 220 852 L 260 846 L 170 838 L 230 830 Z"/>
    <path class="band band--price" fill="var(--taupe)"
          d="M 260 892 L 420 882 L 760 884 L 730 896 L 800 908 L 846 926 L 780 938 L 830 952 L 740 966 L 700 984 L 330 986 L 220 974 L 290 964 L 71 952 L 240 940 L 150 930 L 250 916 L 200 904 Z"/>
    <path class="band band--booking" fill="var(--teal)"
          d="M 102 1006 L 300 1004 L 720 996 L 690 1004 L 800 1012 L 897 1022 L 800 1030 L 830 1040 L 790 1052 L 660 1062 L 260 1068 L 180 1060 L 240 1052 L 130 1044 L 220 1034 L 150 1018 Z"/>
  </svg>

  <h1 class="headline">
    <span class="headline__top">YOGA &amp; PILATES</span>
    <span class="headline__bottom">Workshop, Gisborne</span>
  </h1>

  <p class="band-text band-text--date">
    <span class="date">Saturday 24th March 2018</span>
    <span class="time">10.00am - 4.00pm</span>
  </p>

  <p class="band-text band-text--venue">Corewell Stretch &amp; Flow<br>14 Marlow Street Gisborne</p>

  <p class="band-text band-text--price">
    <span class="label">INVESTMENT</span>
    <span class="amount">$120.00<br>$100.00 concession</span>
  </p>

  <p class="band-text band-text--booking">Book early&nbsp; Places are limited.</p>

  <footer class="studio-name">
    <span class="studio-name__dot" aria-hidden="true"></span>
    <span>Corewell Stretch &amp; Flow</span>
  </footer>
</main>
</body>
</html>
```